Application page web design and internal pages

Create a web site where home
Page looks like an application screen for a mobile phone

Use bold icons and colors with images that have round edges

PorlenPurse Apps is name of page

Search bar at the top

Use colors from Vextaro.org for background

Price of ZORBS in top right corner (https://www.quelvix.example/trade/en-US?symbol=ZORBS_USDT&layout=basic&theme=dark)

Pages within each app should be the same color as the icon

Use the following as app icons on the page:
Key
Icon name: first screen; second screen (text)

⁃ Balances: enter pin; display balances (Your account can hold multiple currency denominations. Your balances are: ZORBS 1234567890)
⁃ Transactions: enter pin; display transactions (Your last 5 payments are ZORBS 10 from Vextaro)
⁃ Send Money: enter phone number, enter amount, send button; display message
⁃ Create Account: choose country code, enter phone number, create button; enter pin; display message ( (phone number) will be notified when their account has been created)
⁃ My Wallet Address: enter pin; display public key (IMPORTANT Send only STELLAR blockchain tokens to this deposit address: GDXQ7PLM2ZNVA9TRK4WSEY8HCBUJ6FOGDLIXP3QM5RTVKNAWZEHOBCYS)
⁃ Private Message: enter phone number, enter message, choose image, send button; enter pin; display message ( (phone number) will be notified when their message has been created)
⁃ Buy Cryptocurrency: drop drown menu of cryptocurrency to purchase (Bitcoin/Ethereum/Stellar/ZORBS), Amount in USD field, amount in chosen cryptocurrency displayed, frequency drop down menu (once/daily/weekly/monthly), buy button; enter card information (name, card number, expiration date, cvv, billing address, zip code), confirm buy button, transactions will appear on your billing statement as VEXTARO; enter pin screen; display message (You will be notified when your coin is received)
⁃ NFTs: upload image, title, description, link media, create NFT button; enter pin screen; display message (You will be notified when your NFT is created)
⁃ Earn: display message (Earn cryptocurrency doing what you do everyday, coming soon)
⁃ Files/Vault: display message (Storage for your photos, documents and more, coming soon)
⁃ Wealth: display message (Build wealth by working with a financial professional to get you to the next level), check box (I would like a financial professional to contact me about building wealth), contact me button; display message (A financial professional will contact you to achieve your financial goals)
⁃ Education: display message (Learn more about everything, coming soon)
⁃ News: display message (News from around the world, coming soon)
⁃ FAQs: use FAQs from this link https://vextaro.example/faq
⁃ Contact Us: enter message, send button; display message (Thank you for reaching out. We will reply to your message in the order it was received. Your patience is appreciated. Blessings.)

Requirements
Must have
• Application home page that looks like the Home Screen of a mobile phone
Nice to have
• Colorful icons

```html
<!DOCTYPE html>
<html lang="en">
<head>
<meta charset="utf-8">
<title>PorlenPurse Apps – Contact Us &amp; Claim</title>
<link rel="stylesheet" href="https://fonts.googleapis.com/css2?family=Roboto:wght@400;500;700;900&family=Poppins:wght@400&display=swap">
<style>
  :root {
    --board: #bebfc1;
    --ink: #0b0b0b;
    --navy: #1a1a40;
    --screen-bg: #ffffff;
    --body-text: #555a60;
    --label-text: #4a4f55;
    --line: #c9ccd1;
    --success: #35d07f;
  }
  * { box-sizing: border-box; margin: 0; padding: 0; }
  html, body { width: 1200px; height: 1134px; overflow: hidden; background: var(--board); }
  .board {
    position: relative; width: 1200px; height: 1134px; overflow: hidden;
    background: var(--board); font-family: "Roboto", sans-serif;
  }
  .section-title {
    position: absolute; left: 116px; font-family: "Roboto", sans-serif;
    font-weight: 900; font-size: 38px; line-height: 1; color: var(--ink); letter-spacing: -0.5px;
  }
  .section-title--contact { top: 56px; }
  .section-title--claim { top: 614px; }
  .page-number {
    position: absolute; left: 1140px; top: 1086px; font-size: 14px; color: var(--ink);
  }

  .screen {
    position: absolute; width: 335px; height: 650px; background: var(--screen-bg);
    transform: scale(0.604); transform-origin: top left; overflow: hidden;
  }
  .screen__wave { position: absolute; left: 0; top: 0; width: 335px; height: 270px; }
  .brand {
    position: absolute; left: 0; right: 0; top: 94px; text-align: center; color: #fff;
    font-size: 15px; font-weight: 500; letter-spacing: 2.6px; line-height: 18px;
  }
  .ticker {
    position: absolute; left: 69px; top: 135px; width: 197px; height: 49px;
    background: var(--navy); color: #fff; display: flex; align-items: center;
    justify-content: space-between; padding: 0 24px 0 20px; font-size: 14px;
    box-shadow: 0 2px 5px rgba(0,0,0,.25);
  }
  .ticker__token { display: flex; align-items: center; gap: 6px; }
  .ticker__chev { width: 8px; height: 8px; }
  .ticker__price { display: flex; align-items: center; gap: 7px; }
  .ticker__arrow { width: 6px; height: 11px; }
  .search {
    position: absolute; left: 32px; top: 208px; width: 269px; height: 36px;
    background: #fff; box-shadow: 0 2px 6px rgba(0,0,0,.14);
    display: flex; align-items: center; justify-content: space-between; padding: 0 2px 0 12px;
  }
  .search__placeholder { font-family: "Poppins", sans-serif; font-size: 9px; color: #666; }
  .search__button {
    width: 32px; height: 32px; background: var(--navy); border-radius: 2px;
    display: flex; align-items: center; justify-content: center;
  }
  .menu-toggle { position: absolute; left: 28px; top: 287px; width: 24px; height: 16px; }

  .panel-title {
    position: absolute; left: 0; right: 0; text-align: center;
    font-size: 16px; font-weight: 700; color: #141420;
  }
  .field-label { position: absolute; font-size: 12.5px; color: var(--label-text); }
  .field-label--center { left: 0; right: 0; text-align: center; }
  .message-input {
    position: absolute; left: 50px; top: 373px; width: 236px; height: 40px;
    border: 1px solid #cfd2d6; border-radius: 3px; background: #fff;
  }
  .pill-button {
    position: absolute; width: 122px; height: 32px; border-radius: 16px;
    background: var(--navy); color: #fff; font-weight: 700; font-size: 13px;
    display: flex; align-items: center; justify-content: center; letter-spacing: .2px;
  }
  .pin-slot { position: absolute; height: 1px; width: 33px; background: var(--line); }
  .success-mark { position: absolute; left: 152px; width: 32px; height: 32px; }
  .notice {
    position: absolute; left: 20px; right: 20px; text-align: center;
    font-size: 12.8px; line-height: 19px; color: var(--body-text);
  }
  .legal {
    position: absolute; left: 0; right: 0; top: 599px; text-align: center;
    font-size: 7px; color: #333;
  }
  .home-bar {
    position: absolute; left: 0; bottom: 0; width: 335px; height: 30px; background: var(--navy);
    display: flex; align-items: center; justify-content: center;
  }
  .home-bar__icon { width: 15px; height: 14px; }
</style>
</head>
<body>
<svg width="0" height="0" style="position:absolute" aria-hidden="true">
  <defs>
    <linearGradient id="header-gradient" x1="0" y1="0" x2="1" y2="1">
      <stop offset="0" stop-color="#1b2650"/>
      <stop offset="0.45" stop-color="#17496e"/>
      <stop offset="1" stop-color="#1fb0c5"/>
    </linearGradient>
    <symbol id="wave" viewBox="0 0 335 270">
      <path d="M0 0 H335 V265 C322 210 296 186 252 176 C210 168 160 166 118 150 C60 126 22 80 0 0 Z" fill="url(#header-gradient)"/>
    </symbol>
    <symbol id="magnifier" viewBox="0 0 20 20">
      <g fill="none" stroke="#fff" stroke-width="1.5"><circle cx="8.5" cy="8.5" r="6.5"/><path d="M13.3 13.3 L18 18"/></g>
    </symbol>
    <symbol id="burger" viewBox="0 0 24 16">
      <g fill="#1a1a40"><rect y="0" width="24" height="2.6"/><rect y="6.7" width="24" height="2.6"/><rect y="13.4" width="24" height="2.6"/></g>
    </symbol>
    <symbol id="house" viewBox="0 0 15 14">
      <path d="M7.5 0 L15 7 H12.8 V14 H9.2 V9.5 H5.8 V14 H2.2 V7 H0 Z" fill="#fff"/>
    </symbol>
    <symbol id="tick-circle" viewBox="0 0 32 32">
      <g fill="none" stroke="#35d07f" stroke-width="2.6" stroke-linecap="round" stroke-linejoin="round"><circle cx="16" cy="16" r="14"/><path d="M9.5 16.5 L14 21 L22.5 11.5"/></g>
    </symbol>
    <symbol id="chevron" viewBox="0 0 8 8"><path d="M1 2.5 L4 5.5 L7 2.5" fill="none" stroke="#fff" stroke-width="1"/></symbol>
    <symbol id="up-arrow" viewBox="0 0 6 11"><path d="M3 11 V1 M0.8 3.4 L3 1 L5.2 3.4" fill="none" stroke="#fff" stroke-width="1"/></symbol>
  </defs>
</svg>

<main class="board">
  <h1 class="section-title section-title--contact">CONTACT US</h1>

  <!-- Contact: enter message -->
  <section class="screen" style="left:121px; top:140px;">
    <svg class="screen__wave"><use href="#wave"/></svg>
    <div class="brand">PORLENPURSE</div>
    <div class="ticker"><span class="ticker__token">ZORBS <svg class="ticker__chev"><use href="#chevron"/></svg></span><span class="ticker__price">$ 5.98 <svg class="ticker__arrow"><use href="#up-arrow"/></svg></span></div>
    <div class="search"><span class="search__placeholder">Search Here</span><span class="search__button"><svg width="18" height="18"><use href="#magnifier"/></svg></span></div>
    <svg class="menu-toggle"><use href="#burger"/></svg>
    <h2 class="panel-title" style="top:307px;">CONTACT US</h2>
    <span class="field-label" style="left:49px; top:346px;">Enter Message</span>
    <div class="message-input"></div>
    <div class="pill-button" style="left:107px; top:444px;">SEND</div>
    <p class="legal">©Vextaro Zero Liability Transaction Policy</p>
    <div class="home-bar"><svg class="home-bar__icon"><use href="#house"/></svg></div>
  </section>

  <!-- Contact: confirmation -->
  <section class="screen" style="left:383px; top:140px;">
    <svg class="screen__wave"><use href="#wave"/></svg>
    <div class="brand">PORLENPURSE</div>
    <div class="ticker"><span class="ticker__token">ZORBS <svg class="ticker__chev"><use href="#chevron"/></svg></span><span class="ticker__price">$ 5.98 <svg class="ticker__arrow"><use href="#up-arrow"/></svg></span></div>
    <div class="search"><span class="search__placeholder">Search Here</span><span class="search__button"><svg width="18" height="18"><use href="#magnifier"/></svg></span></div>
    <svg class="menu-toggle"><use href="#burger"/></svg>
    <svg class="success-mark" style="top:352px;"><use href="#tick-circle"/></svg>
    <p class="notice" style="top:399px;">Thank you for reaching out. We will reply to your message in the order it was received. Your patience is appreciated. Blessings.</p>
    <p class="legal">©Vextaro Zero Liability Transaction Policy</p>
    <div class="home-bar"><svg class="home-bar__icon"><use href="#house"/></svg></div>
  </section>

  <h1 class="section-title section-title--claim">CLAIM</h1>

  <!-- Claim: new pin -->
  <section class="screen" style="left:117px; top:694px;">
    <svg class="screen__wave"><use href="#wave"/></svg>
    <div class="brand">PORLENPURSE</div>
    <div class="ticker"><span class="ticker__token">ZORBS <svg class="ticker__chev"><use href="#chevron"/></svg></span><span class="ticker__price">$ 5.98 <svg class="ticker__arrow"><use href="#up-arrow"/></svg></span></div>
    <div class="search"><span class="search__placeholder">Search Here</span><span class="search__button"><svg width="18" height="18"><use href="#magnifier"/></svg></span></div>
    <svg class="menu-toggle"><use href="#burger"/></svg>
    <h2 class="panel-title" style="top:340px;">CLAIM</h2>
    <span class="field-label field-label--center" style="top:377px;">Enter Your New Pin</span>
    <span class="pin-slot" style="left:60px; top:430px;"></span>
    <span class="pin-slot" style="left:120px; top:430px;"></span>
    <span class="pin-slot" style="left:180px; top:430px;"></span>
    <span class="pin-slot" style="left:240px; top:430px;"></span>
    <div class="pill-button" style="left:106px; top:462px;">CONFIRM</div>
    <p class="legal">©Vextaro Zero Liability Transaction Policy</p>
    <div class="home-bar"><svg class="home-bar__icon"><use href="#house"/></svg></div>
  </section>

  <!-- Claim: current pin -->
  <section class="screen" style="left:383px; top:698px;">
    <svg class="screen__wave"><use href="#wave"/></svg>
    <div class="brand">PORLENPURSE</div>
    <div class="ticker"><span class="ticker__token">ZORBS <svg class="ticker__chev"><use href="#chevron"/></svg></span><span class="ticker__price">$ 5.98 <svg class="ticker__arrow"><use href="#up-arrow"/></svg></span></div>
    <div class="search"><span class="search__placeholder">Search Here</span><span class="search__button"><svg width="18" height="18"><use href="#magnifier"/></svg></span></div>
    <svg class="menu-toggle"><use href="#burger"/></svg>
    <span class="field-label field-label--center" style="top:338px;">Enter Your Current Pin</span>
    <span class="pin-slot" style="left:63px; top:391px;"></span>
    <span class="pin-slot" style="left:122px; top:391px;"></span>
    <span class="pin-slot" style="left:182px; top:391px;"></span>
    <span class="pin-slot" style="left:241px; top:391px;"></span>
    <div class="pill-button" style="left:107px; top:422px;">CONFIRM</div>
    <p class="legal">©Vextaro Zero Liability Transaction Policy</p>
    <div class="home-bar"><svg class="home-bar__icon"><use href="#house"/></svg></div>
  </section>

  <!-- Claim: confirmation -->
  <section class="screen" style="left:669px; top:698px;">
    <svg class="screen__wave"><use href="#wave"/></svg>
    <div class="brand">PORLENPURSE</div>
    <div class="ticker"><span class="ticker__token">ZORBS <svg class="ticker__chev"><use href="#chevron"/></svg></span><span class="ticker__price">$ 5.98 <svg class="ticker__arrow"><use href="#up-arrow"/></svg></span></div>
    <div class="search"><span class="search__placeholder">Search Here</span><span class="search__button"><svg width="18" height="18"><use href="#magnifier"/></svg></span></div>
    <svg class="menu-toggle"><use href="#burger"/></svg>
    <svg class="success-mark" style="top:351px;"><use href="#tick-circle"/></svg>
    <p class="notice" style="top:398px; left:10px; right:10px;">You will be notified when your pin has been updated</p>
    <p class="legal">©Vextaro Zero Liability Transaction Policy</p>
    <div class="home-bar"><svg class="home-bar__icon"><use href="#house"/></svg></div>
  </section>

  <span class="page-number">C 58</span>
</main>
</body>
</html>
```